Agrarhandel benötigt Homepage
Zielgruppe
Wir sind ein Agrarhandel mit einem Warenumschlagslager im Sinne eines klassischen Einzelhandels und vertreiben Produkte an Landwirte.
Wir vertreiben folgende Hauptproduktgruppen:
Einzelfuttermittel
wie z.B. Sojaexktraktionsschrot. Die einzelnen Produkte könnten z.B. wie die Futtermittel auf folgender Seite dargestellt werden (https://www.kornprobe-beispiel.eu/de/produkt/trelomixan)
Mischfuttermittel
Hier bieten wir unseren Kunden an, individuelles Mischfutter auf Basis unserer Einzelfuttermittel herzustellen.
Weitere Details und weitere Produktbereiche habe ich in einer Powerpoint-Übersicht dargestellt.
Neben diesen Produkten wollen wir uns als Familienunternehmen selbst vorstellen. Zudem betreiben wir in unserer Familie zusätzlich einen Milchviehbetrieb den wir ebenfalls hervorheben möchten, da wir unseren Kunden gegenüber einerseits als Zulieferer aber auch als Kollege auftreten wollen.
Einzelfuttermittel: Hier können wir durch unsere Unabhängigkeit punkten, da wir nicht abhängig von bestimmten Lieferanten sind und dementsprechend unabhängig beraten können. Wir untersuchen im Vergleich zu unseren Wettbewerben die Qualität der Futtermittel bis ins Detail und können daher eine Transparenz bieten, die Konkurrenten in der Regel nicht bieten können. Unser Warenumschlagsplatz mit moderner Technik ermöglicht es uns äußerst kosteneffizient die Waren umschlagen und ausliefern zu können.
Mischfuttermittel: Auf Basis der vorhandenen Einzelfuttermittel stellen wir je nach Kundenwunsch individuelle Mischfutter her. Wir arbeiten mit offenen Deklarationen, sodass unsere Kunden jederzeit nachvollziehen können, ob auch die Einzelfuttermittel verwendet wurden, die sie bestellt haben und keine billigen Ersatzprodukte verwendet wurden.
Zudem sind wir BT und HUPA zertifiziert. Die aktuellen für unser Unternehmen ausgestellten Zertifikate müssen für unsere Kunden als Download zur Verfügung stehen. Statt dem HUPA-Logo bitte das ..
Aufgabenstellung
Wir möchten gerne ein zeitgemäße Homepage, jedoch muss auch berücksichtigt werden, dass unsere Kunden eher konservativ denken.

```html
<!DOCTYPE html>
<html lang="de">
<head>
<meta charset="utf-8">
<title>Auental Agrar – Geschäftspartner</title>
<link href="https://fonts.googleapis.com/css2?family=Inter:ital,wght@0,400;0,500;0,700;0,800;1,600&family=Poppins:wght@700&display=swap" rel="stylesheet">
<style>
:root{
  --green:#436117;
  --orange:#f4ac0d;
  --yellow:#f5cd22;
  --frame:#f2c511;
  --grey:#d9d9d9;
  --dark:#232323;
  --ink:#111111;
  --white:#ffffff;
  --badge-green:#5ba92c;
  --badge-blue:#2f78c4;
}
*{margin:0;padding:0;box-sizing:border-box}
html,body{width:766px;height:1200px;overflow:hidden;background:var(--white);font-family:"Inter",sans-serif;color:var(--ink)}
.page{position:relative;width:766px;height:1200px}
.abs{position:absolute}

/* header */
.header-accent{left:0;top:0;width:45px;height:73px;background:var(--orange)}
.header-gap{left:45px;top:0;width:9px;height:73px;background:var(--grey)}
.header-bar{left:54px;top:0;width:712px;height:73px;background:var(--green)}
.header-rule{left:0;top:73px;width:766px;height:6px;background:var(--grey)}
.brand{left:76px;top:14px;width:70px;text-align:center;color:var(--orange);font-weight:700;font-size:9px;line-height:1.15}
.brand .mark{display:block;width:22px;height:22px;margin:0 auto 4px;border-radius:50%;background:var(--orange)}
.nav{left:322px;top:35px;display:flex;gap:10px;font-weight:700;font-size:8.4px;letter-spacing:.1px;color:var(--white)}
.nav .active{color:var(--orange)}
.search{left:730px;top:31px}

/* hero */
.hero{left:60px;top:152px;width:650px;height:569px;border:4px solid var(--frame);
  background:linear-gradient(160deg,#8a7446 0%,#c79a55 30%,#e3b66b 50%,#a86b2c 75%,#5b3316 100%);
  box-shadow:0 10px 30px rgba(0,0,0,.35)}
.glass{left:115px;top:196px;width:538px;height:481px;border-radius:27px;
  background:linear-gradient(180deg,rgba(220,190,130,.55) 0%,rgba(170,120,70,.55) 50%,rgba(90,60,40,.5) 100%);
  border-bottom:1.5px solid var(--white)}
.hero-title{left:115px;top:346px;width:538px;text-align:center;font-family:"Poppins",sans-serif;font-weight:700;font-size:32px;color:var(--white)}
.partner{top:448px;display:flex;flex-direction:column;align-items:center;gap:5px;font-weight:700;font-size:10px;color:var(--white)}
.partner .dot{width:44px;height:44px;border-radius:50%}
.partner-a{left:262px;width:100px}
.partner-a .dot{background:#1c2a7a}
.partner-b{left:391px;width:120px}
.partner-b .dot{background:#f06a05}

/* certificates */
.cert{display:flex;flex-direction:column;align-items:center;gap:4px;font-weight:700;font-size:11px;color:var(--ink)}
.cert-a{left:66px;top:792px;width:96px}
.cert-b{left:255px;top:793px;width:100px}
.badge-a{width:86px;height:86px;border-radius:6px;background:var(--badge-green);border:3px solid #e8efe0}
.badge-b{position:relative;width:68px;height:77px;background:var(--white);border:1px solid var(--badge-blue)}
.badge-b span{position:absolute;left:12px;top:10px;width:42px;height:42px;border-radius:50%;background:var(--badge-blue)}
.und{left:190px;top:818px;font-weight:500;font-size:12px}
.certified{left:154px;top:885px;width:120px;text-align:center;font-style:italic;font-weight:600;font-size:21px}
.download{left:471px;top:798px;width:238px;height:65px;border-radius:32px;background:var(--orange);
  box-shadow:3px 4px 6px rgba(0,0,0,.25);display:flex;align-items:center;justify-content:center;text-align:center;
  font-weight:800;font-size:17px;line-height:1.3;color:var(--ink)}

/* footer */
.footer{left:0;top:958px;width:766px;height:210px;background:var(--dark)}
.foot-brand{left:85px;top:1010px;width:101px;text-align:center;color:var(--orange);font-weight:700;font-size:16px;line-height:1.15}
.foot-brand .mark{display:block;width:44px;height:44px;margin:0 auto 8px;border-radius:50%;background:var(--orange)}
.vline{top:1000px;width:2px;height:88px;background:var(--white)}
.vline::before,.vline::after{content:"";position:absolute;left:-2px;width:6px;height:6px;border-radius:50%;background:var(--white)}
.vline::before{top:-3px}.vline::after{bottom:-3px}
.news-title{left:253px;top:1000px;font-weight:700;font-size:12.5px;color:var(--white)}
.news-title b{font-size:16px}
.field{height:14px;background:var(--grey);font-size:6px;padding:3px 6px;color:#222}
.f-name{left:252px;top:1025px;width:81px}
.f-mail{left:343px;top:1025px;width:80px}
.f-tel{left:433px;top:1025px;width:81px}
.f-msg{left:252px;top:1050px;width:171px;height:21px;padding-top:7px}
.send{left:433px;top:1057px;width:81px;height:14px;border-radius:4px;background:var(--yellow);font-weight:800;font-size:7px;display:flex;align-items:center;justify-content:center}
.contact{left:560px;top:1029px;list-style:none;font-size:6.8px;color:var(--white)}
.contact li{display:flex;align-items:center;gap:6px;height:12px}
.contact svg{width:7px;height:7px}
.reach{left:291px;top:1101px;font-weight:700;font-size:12.5px;color:var(--white)}
.reach span{color:var(--orange)}
.msg-dot{left:457px;top:1093px;width:32px;height:32px;border-radius:50%;background:#2fb34a}
.socials{left:354px;top:1143px;display:flex;gap:4px}
.socials span{width:12px;height:12px;border-radius:3px;background:var(--white)}
.bottom{left:0;top:1168px;width:766px;height:32px;background:var(--yellow);display:flex;align-items:center;justify-content:center;font-weight:500;font-size:7px}
</style>
</head>
<body>
<div class="page">
  <header>
    <div class="abs header-accent"></div>
    <div class="abs header-gap"></div>
    <div class="abs header-bar"></div>
    <div class="abs header-rule"></div>
    <div class="abs brand"><span class="mark"></span>Auental Agrar</div>
    <nav class="abs nav">
      <span class="active">LANDWIRT</span>
      <span>GESCHÄFTSPARTNER</span>
      <span>LIEFERANTEN</span>
      <span>PRODUKTE ⌄</span>
      <span>FIRMENPRÄSENTATION</span>
    </nav>
    <svg class="abs search" width="16" height="16" viewBox="0 0 16 16" fill="none" stroke="#fff" stroke-width="1.5"><circle cx="6.5" cy="6.5" r="5"/><line x1="10.2" y1="10.2" x2="15" y2="15"/></svg>
  </header>

  <section>
    <div class="abs hero" role="img" aria-label="Foto: Mähdrescher bei der Weizenernte im goldenen Abendlicht"></div>
    <div class="abs glass"></div>
    <h1 class="abs hero-title">Geschäftspartner</h1>
    <div class="abs partner partner-a"><span class="dot"></span>Brennhof</div>
    <div class="abs partner partner-b"><span class="dot"></span>Saatwerk Lindner</div>
  </section>

  <section>
    <div class="abs cert cert-a">
      <div class="badge-a" role="img" aria-label="Zertifikatssiegel HUPA"></div>
      <span>HUPA</span>
    </div>
    <div class="abs und">und</div>
    <div class="abs cert cert-b">
      <div class="badge-b" role="img" aria-label="Zertifikatssiegel BT"><span></span></div>
      <span>BT</span>
    </div>
    <div class="abs certified">zertifiziert</div>
    <div class="abs download">HERUNTERLADEN<br>ZERTIFIKAT</div>
  </section>

  <footer>
    <div class="abs footer"></div>
    <div class="abs foot-brand"><span class="mark"></span>Auental Agrar</div>
    <div class="abs vline" style="left:227px"></div>
    <div class="abs vline" style="left:537px"></div>
    <div class="abs news-title">Abonnieren Sie Unseren <b>Newsletter</b></div>
    <div class="abs field f-name">Name</div>
    <div class="abs field f-mail">Email</div>
    <div class="abs field f-tel">Telefonnummer</div>
    <div class="abs field f-msg">Nachricht</div>
    <div class="abs send">SCHICKEN</div>
    <ul class="abs contact">
      <li><svg viewBox="0 0 8 8"><path d="M4 0a3 3 0 0 0-3 3c0 2 3 5 3 5s3-3 3-5a3 3 0 0 0-3-3z" fill="#fff"/></svg>Standort</li>
      <li><svg viewBox="0 0 8 8"><circle cx="4" cy="4" r="3.5" fill="#fff"/></svg>+49 7000 123456</li>
      <li><svg viewBox="0 0 8 8"><rect x="0" y="1.5" width="8" height="5" fill="#fff"/></svg>kontakt@auental-agrar.de</li>
    </ul>
    <div class="abs reach"><span>Kontaktieren Sie Uns</span> per</div>
    <div class="abs msg-dot"></div>
    <div class="abs socials"><span></span><span></span><span></span><span></span></div>
    <div class="abs bottom">Copyright 2023 All Right Reserved</div>
  </footer>
</div>
</body>
</html>
```